Telecommunications/Power civil contractor needs business card design

Were a new telecommunications/power underground civil contractor that is looking for a new business card design. Our company colours are silver or grey and orange. Feel free to use the white background logo or the black background logo.

Target Market(s)

Local contractors, utility companies, private sector mining/energy companies, developers.

Industry/Entity Type

Telecommunications

Contact Information for Business Card

Each card will need the following info:
Persons name:
Title:
E-mail:
Phone number:
Shop Address:
Mailing Address:

Requirements
Must have
• Each card will need the following info:
• Persons name:
• Title:
• E-mail:
• Phone number:
• Shop Address:
• Mailing Address:

```html
<!DOCTYPE html>
<html lang="en">
<head>
<meta charset="utf-8">
<title>Ternline Contracting Inc – Business Card</title>
<link rel="stylesheet" href="https://fonts.googleapis.com/css2?family=Open+Sans:wght@400;600;700&display=swap">
<style>
  :root {
    --orange: #f0612a;
    --orange-light: #f57a45;
    --grey: #7d7f82;
    --grey-dark: #55585b;
    --white: #ffffff;
    --paper: #f3f3f3;
    --backdrop: #e6e3de;
  }
  * { box-sizing: border-box; margin: 0; padding: 0; }
  html, body {
    width: 1200px;
    height: 843px;
    overflow: hidden;
    background: var(--backdrop);
    font-family: "Open Sans", sans-serif;
  }
  .stage {
    position: relative;
    width: 1200px;
    height: 843px;
  }
  .card {
    position: absolute;
    top: 267px;
    width: 540px;
    height: 309px;
    background: var(--white);
    box-shadow: 0 6px 18px rgba(0,0,0,0.18);
    overflow: hidden;
  }
  .card--back { left: 40px; background: linear-gradient(160deg, var(--white) 0%, var(--paper) 100%); }
  .card--front { left: 620px; }

  /* shared brand */
  .brand-dot {
    border-radius: 50%;
    background: var(--orange);
    flex: none;
  }
  .brand-name {
    font-weight: 700;
    color: var(--grey-dark);
    text-transform: uppercase;
    letter-spacing: 0.04em;
  }

  /* back */
  .brand-centered {
    position: absolute;
    inset: 0;
    display: flex;
    align-items: center;
    justify-content: center;
    gap: 14px;
  }
  .brand-centered .brand-dot { width: 34px; height: 34px; }
  .brand-centered .brand-name { font-size: 24px; }

  /* front */
  .front-panel {
    position: absolute;
    left: 0;
    top: 0;
    width: 258px;
    height: 100%;
    background: linear-gradient(100deg, var(--orange) 0%, var(--orange-light) 70%, var(--orange) 100%);
    color: var(--white);
    padding: 26px 24px;
  }
  .person-name {
    font-size: 18px;
    font-weight: 600;
    letter-spacing: 0.03em;
    text-transform: uppercase;
  }
  .person-title {
    font-size: 13px;
    margin-top: 1px;
  }
  .contact {
    position: absolute;
    left: 24px;
    bottom: 30px;
    font-size: 13px;
    line-height: 21px;
  }
  .contact-line {
    display: flex;
    align-items: center;
    gap: 9px;
  }
  .contact-line svg { width: 12px; height: 12px; flex: none; }
  .address { margin-bottom: 4px; }

  .front-divider {
    position: absolute;
    left: 270px;
    top: 0;
    width: 5px;
    height: 100%;
    background: var(--grey);
  }
  .brand-corner {
    position: absolute;
    left: 295px;
    right: 20px;
    bottom: 44px;
    display: flex;
    flex-direction: column;
    align-items: center;
    gap: 10px;
    text-align: center;
  }
  .brand-corner .brand-dot { width: 44px; height: 44px; }
  .brand-corner .brand-name { font-size: 18px; line-height: 22px; }
</style>
</head>
<body>
<main class="stage">

  <section class="card card--back" aria-label="Card back">
    <div class="brand-centered">
      <span class="brand-dot"></span>
      <span class="brand-name">Ternline Contracting Inc</span>
    </div>
  </section>

  <section class="card card--front" aria-label="Card front">
    <div class="front-panel">
      <p class="person-name">Dana Holloway</p>
      <p class="person-title">CEO/Founder</p>

      <div class="contact">
        <p class="address">4120 Birchwood Road<br>Fairbanks, Alaska 99701</p>
        <p class="contact-line">
          <svg viewBox="0 0 24 24"><path fill="currentColor" d="M6.6 10.8a15.1 15.1 0 0 0 6.6 6.6l2.2-2.2a1 1 0 0 1 1-.25 11.4 11.4 0 0 0 3.6.57 1 1 0 0 1 1 1V20a1 1 0 0 1-1 1A17 17 0 0 1 3 4a1 1 0 0 1 1-1h3.5a1 1 0 0 1 1 1c0 1.25.2 2.45.57 3.57a1 1 0 0 1-.25 1z"/></svg>
          907 555 0148
        </p>
        <p class="contact-line">
          <svg viewBox="0 0 24 24"><path fill="currentColor" d="M2 5h20v14H2z"/><path fill="none" stroke="#f0612a" stroke-width="2" d="M2 5l10 8 10-8"/></svg>
          dana@ternline.com
        </p>
        <p class="contact-line">
          <svg viewBox="0 0 24 24"><circle cx="12" cy="12" r="10" fill="currentColor"/><path fill="none" stroke="#f0612a" stroke-width="1.6" d="M2 12h20M12 2c3 3 3 17 0 20M12 2c-3 3-3 17 0 20"/></svg>
          www.ternline.com
        </p>
      </div>
    </div>

    <div class="front-divider"></div>

    <div class="brand-corner">
      <span class="brand-dot"></span>
      <span class="brand-name">Ternline<br>Contracting Inc</span>
    </div>
  </section>

</main>
</body>
</html>
```